Veltrane Group Business Card Design

The CEO is looking for a new trendy look for his business card.
You can stay with current branding or come up with something new/creative. It can be 3D, including Medical Office buildings. You can use our logo in a variety of colors. Please include name, title, company name, company website, email address, cell number

Target Market(s)

Real Estate Development and Construction

Industry/Entity Type

Health care real estate

Contact Information for Business Card

Rohesh Kamdar, CEO M-604.781.2249 E-roheshkamdar@veltrane.com Address:4180 Lindqvist Ave, Tampa, FL 33482 www.veltrane.com

Font styles to use
Other font styles liked:
• Be creative

Requirements
Must have
• Creative, trendy look
Nice to have
• Please go to our website to get a feel- www. veltrane.com
Should not have
• small fonts

```html
<!DOCTYPE html>
<html lang="en">
<head>
<meta charset="utf-8">
<title>Veltrane Group Business Card</title>
<link href="https://fonts.googleapis.com/css2?family=Montserrat:wght@400;500;700;800&display=swap" rel="stylesheet">
<style>
  :root {
    --bg: #ccd1d1;
    --card: #f1f0ee;
    --red: #b31f29;
    --red-line: #e0322b;
    --ink: #2b2b2b;
    --muted: #4a4a4a;
  }
  * { margin: 0; padding: 0; box-sizing: border-box; }
  html, body {
    width: 1200px; height: 881px; overflow: hidden;
    background: var(--bg);
    font-family: "Montserrat", sans-serif;
  }
  .sheet {
    width: 1200px; height: 881px;
    display: flex; align-items: center; justify-content: center; gap: 48px;
  }
  .card {
    position: relative;
    width: 525px; height: 300px;
    background: var(--card);
    border-bottom: 4px solid var(--red);
    box-shadow: 0 14px 30px rgba(0,0,0,0.18);
  }
  /* Front: contact side */
  .holder { position: absolute; left: 34px; top: 46px; }
  .holder-name {
    color: var(--red); font-weight: 700; font-size: 19px; letter-spacing: 0.02em;
    text-transform: uppercase;
  }
  .holder-title { color: var(--muted); font-size: 12px; margin-top: 3px; }
  .address { position: absolute; left: 34px; top: 128px; color: var(--ink); font-size: 13px; }
  .wordmark-small {
    position: absolute; right: 34px; top: 42px; text-align: right;
    color: var(--red); font-weight: 800; font-size: 36px; line-height: 0.95; letter-spacing: -0.01em;
  }
  .divider { position: absolute; left: 34px; right: 34px; top: 190px; height: 1px; background: var(--red-line); }
  .contacts {
    position: absolute; left: 34px; right: 34px; top: 212px;
    display: flex; flex-wrap: wrap; gap: 6px 16px; color: var(--ink); font-size: 12.5px;
  }
  .contact { display: flex; align-items: center; gap: 6px; }
  .contact svg { width: 11px; height: 11px; flex: none; }
  /* Back: brand side */
  .card-back { display: flex; align-items: center; justify-content: center; }
  .wordmark-large {
    color: var(--red); font-weight: 800; font-size: 62px; line-height: 0.95;
    letter-spacing: -0.01em; text-align: right;
  }
</style>
</head>
<body>
<main class="sheet">
  <section class="card card-front">
    <div class="holder">
      <p class="holder-name">Rohesh Kamdar</p>
      <p class="holder-title">CEO</p>
    </div>
    <p class="wordmark-small">Veltrane<br>Group</p>
    <p class="address">4180 Lindqvist Ave, Tampa, FL 33482</p>
    <div class="divider"></div>
    <div class="contacts">
      <span class="contact">
        <svg viewBox="0 0 12 12"><rect x="3" y="0.5" width="6" height="11" rx="1" fill="none" stroke="#b31f29" stroke-width="1.2"/></svg>
        604.781.2249
      </span>
      <span class="contact">
        <svg viewBox="0 0 12 12"><rect x="0.5" y="2.5" width="11" height="7" fill="#b31f29"/><path d="M0.5 2.5 L6 6.5 L11.5 2.5" fill="none" stroke="#f1f0ee" stroke-width="1"/></svg>
        roheshkamdar@veltrane.com
      </span>
      <span class="contact">
        <svg viewBox="0 0 12 12"><circle cx="6" cy="6" r="5.5" fill="#b31f29"/><path d="M0.5 6 H11.5 M6 0.5 C3 3.5 3 8.5 6 11.5 M6 0.5 C9 3.5 9 8.5 6 11.5" fill="none" stroke="#f1f0ee" stroke-width="0.8"/></svg>
        www.veltrane.com
      </span>
    </div>
  </section>
  <section class="card card-back">
    <p class="wordmark-large">Veltrane<br>Group</p>
  </section>
</main>
</body>
</html>
```